Card Design Project

We are looking for a couple card / box designs that will for a new company that is in the bereavement assistance industry.
Our customers are churches, counseling centers and funeral homes.
Once we have these card designs we will need to work with that same artist to help us out with box graphic designs that are similar to the card designs. The box is 12" long x 4" wide x 6" high
We will need more designs in the future so we are looking for an artist for future work.
Our look needs to be professional and solemn.
The front of the card should be quite close to what i am attaching but with some professional touches to it that give it a proper look. We dont want you to stray to far from what i have attached but if you feel you have some good ideas we would be more than happy to see them.
The back of the card we want people to be able to leave the family a note so will need wording such as "leave a message to the family" or "write a memory"
Keep in mind we will need this look to be able to match graphics on the box as well, we kind of need the card design and box design to go together.
Thanks
Just wanted to mention to all designers that although we would like our logo on the card it is something that we need to keep kind of in the background somehow. We cant be seen as trying to push a brand name too much so please keep that in mind. Thanks
Designers, I took the need to see what the design looked like on a box out.
Target Market(s)
Funeral homes, churches, counseling centers
Industry/Entity Type
Industry
Requirements
Must have
- Professional and solemn look
Card need to be 4"wide X 6" high and needs to be portrait
A pin will be attached to the top right part of the card so will need a space there for it.
I was thinking that we would have the pic of the ribbon symbol there so when the pin is off the card there would still be a ribbon pic there. The pins that we will be attaching are ribbon pins similar to what i have on my pdf's
Please keep in mind that we cant really have out logo in a dominant area on the card. We would like to have it subtly in there but not to where it is in your face type of thing.
Nice to have
- Our logo but very small, not to intrusive .
Would like 2 designs, one dark and another light.
Maybe 1 masculine or gender neutral and another feminine
Wording should be the same

```html
<!DOCTYPE html>
<html lang="en">
<head>
<meta charset="utf-8">
<title>Memorial Cards – Light and Dark</title>
<link href="https://fonts.googleapis.com/css2?family=Source+Sans+3:ital,wght@0,300;0,400;1,300&display=swap" rel="stylesheet">
<style>
  :root {
    --page: #ffffff;
    --light-bg-a: #ebebeb;
    --light-bg-b: #d2d2d2;
    --light-text: #1e1e1e;
    --dark-bg: #050505;
    --dark-text: #f2f2f2;
    --back-light: #f4f4f4;
    --back-grey: #e4e4e4;
    --mark-grey: #8a8a8a;
    --card-shadow: rgba(0,0,0,0.18);
  }
  * { margin: 0; padding: 0; box-sizing: border-box; }
  html, body {
    width: 1200px; height: 819px; overflow: hidden;
    background: var(--page);
    font-family: "Source Sans 3", "Myriad Pro", sans-serif;
  }
  .sheet { position: relative; width: 1200px; height: 819px; }

  /* portrait cards, 4 wide x 6 high */
  .card {
    position: absolute; width: 256px; height: 384px; overflow: hidden;
    box-shadow: 0 0 3px var(--card-shadow);
  }
  .card--front-light { left: 339px; top: 20px; background: radial-gradient(ellipse at 60% 40%, var(--light-bg-a), var(--light-bg-b)); color: var(--light-text); }
  .card--back-light { left: 605px; top: 20px; background: radial-gradient(ellipse at 50% 40%, #fbfbfb, var(--back-light) 70%, #e9e9e9); color: var(--light-text); }
  .card--front-dark { left: 339px; top: 414px; background: var(--dark-bg); color: var(--dark-text); }
  .card--back-dark { left: 605px; top: 414px; background: var(--back-grey); color: var(--light-text); }

  .photo { position: absolute; }
  .photo--flower { right: 0; bottom: 0; width: 130px; height: 170px;
    background: radial-gradient(ellipse at 45% 55%, rgba(255,255,255,0.9), rgba(240,240,240,0.4) 55%, transparent 75%); }
  .photo--flower-faint { left: 30px; top: 150px; width: 180px; height: 210px;
    background: radial-gradient(ellipse at 50% 50%, rgba(225,225,225,0.8), transparent 70%); }
  .photo--forest { left: 110px; top: 0; width: 146px; height: 384px;
    background: linear-gradient(100deg, #050505 0%, #1a1a1a 25%, #6a6a6a 50%, #2a2a2a 68%, #080808 90%); }
  .photo--forest-faint { left: 50px; top: 0; width: 160px; height: 384px;
    background: linear-gradient(100deg, transparent 0%, rgba(255,255,255,0.5) 45%, rgba(255,255,255,0.2) 65%, transparent 100%); }

  .pin-spot { position: absolute; right: 16px; top: 18px; width: 84px; display: flex; flex-direction: column; align-items: center; gap: 6px; }
  .pin-spot__square { width: 48px; height: 48px; background: var(--mark-grey); opacity: 0.35; }
  .brand-name { font-size: 13px; line-height: 13px; font-weight: 400; color: var(--mark-grey); text-align: center; text-transform: uppercase; letter-spacing: 0.4px; }

  .greeting { position: absolute; left: 22px; top: 118px; font-weight: 300; font-style: italic; font-size: 28px; line-height: 32px; letter-spacing: 0.3px; }
  .message { position: absolute; left: 22px; top: 164px; width: 212px; font-size: 10.5px; line-height: 13px; font-weight: 400; }
  .message p { margin-bottom: 11px; }
  .closing { position: absolute; left: 22px; top: 334px; font-size: 10.5px; line-height: 13px; }

  .prompt { position: absolute; left: 0; right: 0; top: 92px; text-align: center; font-style: italic; font-weight: 300; font-size: 19px; }
</style>
</head>
<body>
<main class="sheet">
  <section class="card card--front-light">
    <div class="photo photo--flower" role="img" aria-label="White daisy with scattered petals on a pale grey textured background"></div>
    <div class="pin-spot"><span class="pin-spot__square"></span><span class="brand-name">Mourning<br>Circle</span></div>
    <h1 class="greeting">Dear Friends</h1>
    <div class="message">
      <p>Your support in attending this memorial and celebration of life means so much to us.</p>
      <p>Our loved one has touched you in ways we may not even recognize yet.</p>
      <p>We invite you to wear this pin through your grieving process, which we receive as a symbol of your sympathy and support of our loss</p>
    </div>
    <p class="closing">Thank you for grieving<br>together with us</p>
  </section>

  <section class="card card--back-light">
    <div class="photo photo--flower-faint" role="img" aria-label="Faded white daisy on a white textured background"></div>
    <p class="prompt">write a memory</p>
  </section>

  <section class="card card--front-dark">
    <div class="photo photo--forest" role="img" aria-label="Black and white forest path with sunlight streaming through the trees"></div>
    <div class="pin-spot"><span class="pin-spot__square"></span><span class="brand-name">Mourning<br>Circle</span></div>
    <h1 class="greeting">Dear Friends</h1>
    <div class="message">
      <p>Your support in attending this memorial and celebration of life means so much to us.</p>
      <p>Our loved one has touched you in ways we may not even recognize yet.</p>
      <p>We invite you to wear this pin through your grieving process, which we receive as a symbol of your sympathy and support of our loss</p>
    </div>
    <p class="closing">Thank you for grieving<br>together with us</p>
  </section>

  <section class="card card--back-dark">
    <div class="photo photo--forest-faint" role="img" aria-label="Faded light forest path with sunbeams on a grey background"></div>
    <p class="prompt">write a memory</p>
  </section>
</main>
</body>
</html>
```